Local Flower Farm Needs Business Card Design

I need business cards designed for a flower farm based in Eudora, Kansas.
Business Info:
We are a local cut flower farm located in Eudora, Kansas, founded by Corinne Haldwick. What started as a passion for agriculture and search for more joy in daily life has blossomed into a small business dedicated to providing the community with beautiful, fresh, and sustainable flowers. We specialize in local, seasonal blooms, ensuring that every petal reflects the care and dedication we pour into our craft. Our mission is to deliver the highest quality flowers directly to our customers through local farmers markets and to florists who share our commitment to sustainability. Join us in celebrating the beauty of nature, one bloom at a time!
Contact Details:
Corinne Haldwick
Owner
Phone 913-555-0147
Facebook: Rosalind Thorpe Gardens
Instagram: @RosalindThorpeGardens
Website: RosalindThorpeGardens.example
Target Market(s)
Wholesale to Florists and Direct to Consumer via Farmers Market
Industry/Entity Type
Florist, Farm
Contact Information for Business Card
Name, Contact Info, Logo
Look and feel
Each slider illustrates characteristics of the customer's brand and the style your logo design should communicate.

```html
<!DOCTYPE html>
<html lang="en">
<head>
<meta charset="utf-8">
<title>Rosalind Thorpe Gardens – Business Card</title>
<link href="https://fonts.googleapis.com/css2?family=Montserrat:wght@300;400;700&display=swap" rel="stylesheet">
<style>
  :root {
    --ink: #0f2a2c;
    --paper: #ffffff;
    --backdrop: #ebebeb;
    --text: #1c1c1c;
  }
  * { margin: 0; padding: 0; box-sizing: border-box; }
  html, body {
    width: 1200px; height: 1108px; overflow: hidden;
    background: var(--backdrop);
    font-family: "Montserrat", sans-serif;
  }
  .card {
    position: absolute;
    background: var(--paper);
    overflow: hidden;
  }
  .card--front { left: 219px; top: 51px; width: 774px; height: 472px; }
  .card--back  { left: 217px; top: 569px; width: 776px; height: 456px; }

  .name-band {
    position: absolute; left: 0; top: 40px; width: 100%; height: 84px;
    background: var(--ink);
  }
  .holder {
    position: absolute; right: 50px; top: 52px; text-align: right; color: var(--paper);
  }
  .holder__name { font-weight: 700; font-size: 28px; letter-spacing: 0.3px; line-height: 1.1; }
  .holder__role { font-weight: 300; font-size: 17px; margin-top: 2px; }

  .brand-seal {
    position: absolute; left: 79px; top: 19px; width: 126px; height: 126px;
    border-radius: 50%; background: var(--paper);
    border: 2px solid var(--ink);
    display: flex; align-items: center; justify-content: center; text-align: center;
  }
  .brand-seal__name {
    color: var(--ink); font-weight: 700; font-size: 14px; line-height: 1.2; text-transform: uppercase;
  }

  .contact-list {
    position: absolute; left: 40px; top: 334px; list-style: none;
    color: var(--text); font-size: 17px; font-weight: 400;
  }
  .contact-list li { display: flex; align-items: center; height: 28.5px; }
  .contact-list svg { width: 17px; height: 17px; margin-right: 9px; flex: none; }

  .brand-mark {
    position: absolute; right: 54px; top: 225px; text-align: right;
    color: var(--ink); font-weight: 700; font-size: 50px; line-height: 1.05;
  }

  .brand-emblem {
    position: absolute; left: 228px; top: 65px; width: 340px; height: 340px;
    border-radius: 50%; border: 2px solid var(--ink);
    display: flex; align-items: center; justify-content: center; text-align: center;
  }
  .brand-emblem__name {
    color: var(--ink); font-weight: 700; font-size: 40px; line-height: 1.15; text-transform: uppercase;
  }
</style>
</head>
<body>

<section class="card card--front">
  <div class="name-band"></div>
  <div class="brand-seal"><span class="brand-seal__name">Rosalind<br>Thorpe<br>Gardens</span></div>
  <div class="holder">
    <div class="holder__name">Corinne Haldwick</div>
    <div class="holder__role">Owner</div>
  </div>

  <ul class="contact-list">
    <li>
      <svg viewBox="0 0 24 24" aria-hidden="true"><path fill="#1c1c1c" d="M6.6 10.8a15.1 15.1 0 0 0 6.6 6.6l2.2-2.2a1 1 0 0 1 1-.25 11.4 11.4 0 0 0 3.6.57 1 1 0 0 1 1 1V20a1 1 0 0 1-1 1A17 17 0 0 1 3 4a1 1 0 0 1 1-1h3.5a1 1 0 0 1 1 1c0 1.25.2 2.45.57 3.57a1 1 0 0 1-.25 1z"/></svg>
      913-555-0147
    </li>
    <li>
      <svg viewBox="0 0 24 24" aria-hidden="true"><circle cx="12" cy="12" r="10" fill="#1c1c1c"/></svg>
      Rosalind Thorpe Gardens
    </li>
    <li>
      <svg viewBox="0 0 24 24" aria-hidden="true"><circle cx="12" cy="12" r="10" fill="#1c1c1c"/></svg>
      @RosalindThorpeGardens
    </li>
    <li>
      <svg viewBox="0 0 24 24" aria-hidden="true"><g fill="none" stroke="#1c1c1c" stroke-width="2"><circle cx="12" cy="12" r="10"/><ellipse cx="12" cy="12" rx="4" ry="10"/><path d="M2 12h20"/></g></svg>
      www.RosalindThorpeGardens.example
    </li>
  </ul>

  <div class="brand-mark">Rosalind<br>Thorpe<br>Gardens</div>
</section>

<section class="card card--back">
  <div class="brand-emblem"><span class="brand-emblem__name">Rosalind<br>Thorpe<br>Gardens</span></div>
</section>

</body>
</html>
```